Business card for medical clinic

I need an upmarket, modern medical/health business card for my clinic

Contact Information for Business Card

name, address, email, qr code

```html
<!DOCTYPE html>
<html lang="en">
<head>
<meta charset="utf-8">
<title>Lumen Health Group – Business Card</title>
<link href="https://fonts.googleapis.com/css2?family=Cinzel:wght@600&family=Gelasio:wght@400&display=swap" rel="stylesheet">
<style>
  :root {
    --bg: #d2d3d5;
    --card: #ffffff;
    --navy: #1b3050;
    --brand-blue: #1d5d8f;
    --sky: #1ea3dc;
    --ink: #1e1e1e;
  }
  * { margin: 0; padding: 0; box-sizing: border-box; }
  html, body { width: 900px; height: 1200px; overflow: hidden; }
  body { background: var(--bg); position: relative; font-family: "Gelasio", Georgia, serif; color: var(--ink); }

  .card {
    position: absolute;
    left: 133px;
    width: 633px;
    height: 364px;
    background: var(--card);
  }
  .card--front { top: 210px; }
  .card--back { top: 624px; }

  .brand {
    position: absolute;
    display: flex;
    align-items: center;
    gap: 12px;
    transform: translateX(-50%);
    white-space: nowrap;
  }
  .brand__dot { border-radius: 50%; background: var(--sky); flex: none; }
  .brand__name { font-family: "Cinzel", "Times New Roman", serif; font-weight: 600; color: var(--brand-blue); }

  .card--front .brand { left: 316px; top: 160px; }
  .card--front .brand__dot { width: 34px; height: 34px; }
  .card--front .brand__name { font-size: 32px; letter-spacing: 1px; }

  .contact {
    position: absolute;
    left: 0; right: 0;
    text-align: center;
  }
  .contact__name {
    position: absolute; left: 0; right: 0; top: 66px;
    font-family: "Cinzel", "Times New Roman", serif; font-weight: 600;
    font-size: 21px; color: var(--brand-blue); letter-spacing: 0.3px;
  }
  .contact__role {
    position: absolute; left: 50%; top: 94px; transform: translateX(-50%);
    display: flex; align-items: center; gap: 6px;
    font-size: 15px; color: var(--sky); white-space: nowrap;
  }
  .contact__role::before, .contact__role::after {
    content: ""; width: 50px; height: 1.5px; background: var(--sky);
  }
  .contact__address { position: absolute; left: 0; right: 0; top: 127px; font-size: 15px; line-height: 22px; }
  .contact__icons { position: absolute; left: 50%; top: 180px; transform: translateX(-50%); display: flex; gap: 6px; }
  .contact__icons svg { width: 12px; height: 12px; }
  .contact__phone { position: absolute; left: 0; right: 0; top: 204px; font-size: 15px; letter-spacing: 2.5px; }
  .contact__email { position: absolute; left: 0; right: 0; top: 228px; font-size: 15px; }
  .contact__web { position: absolute; left: 0; right: 0; top: 253px; font-size: 15px; }

  .card--back .brand { left: 316px; top: 298px; gap: 7px; }
  .card--back .brand__dot { width: 14px; height: 14px; }
  .card--back .brand__name { font-size: 13px; }
</style>
</head>
<body>
  <section class="card card--front" aria-label="Card front">
    <div class="brand">
      <span class="brand__dot"></span>
      <span class="brand__name">Lumen Health Group</span>
    </div>
  </section>

  <section class="card card--back" aria-label="Card back">
    <div class="contact">
      <h1 class="contact__name">DANIEL HARPER</h1>
      <p class="contact__role">Principal Consultant</p>
      <p class="contact__address">PO Box 418520<br>Cedar Hollow, Alaska 99580</p>
      <div class="contact__icons" aria-hidden="true">
        <svg viewBox="0 0 12 12"><path d="M2.5 1 L4.5 1 L5.2 3.6 L4 4.6 Q5 7 7.4 8 L8.4 6.8 L11 7.5 L11 9.5 Q10.5 11 9 11 Q1 10 1 2.5 Q1 1 2.5 1Z" fill="var(--brand-blue)"/></svg>
        <svg viewBox="0 0 12 12"><rect x="0.5" y="2.5" width="11" height="7.5" fill="var(--brand-blue)"/><path d="M0.8 2.8 L6 7 L11.2 2.8" stroke="#fff" stroke-width="1" fill="none"/></svg>
        <svg viewBox="0 0 12 12"><g fill="none" stroke="var(--brand-blue)" stroke-width="1"><circle cx="6" cy="6" r="5"/><ellipse cx="6" cy="6" rx="2.2" ry="5"/><line x1="1" y1="6" x2="11" y2="6"/><line x1="6" y1="1" x2="6" y2="11"/></g></svg>
      </div>
      <p class="contact__phone">+1-907-555-0142</p>
      <p class="contact__email">hello@lumenhealthgroupcare.com</p>
      <p class="contact__web">www.lumenhealthgroupcare.com</p>
    </div>
    <div class="brand">
      <span class="brand__dot"></span>
      <span class="brand__name">Lumen Health Group</span>
    </div>
  </section>
</body>
</html>
```